Mindfulness School for Children -- Business Cards

We're looking for business cards for our school directors and owners. We're a mindfulness school for children called little lanterns. Attached are our logos/icons.

```html
<!DOCTYPE html>
<html lang="en">
<head>
<meta charset="utf-8">
<title>little lanterns — Business Cards</title>
<link href="https://fonts.googleapis.com/css2?family=Alegreya:wght@400;500&family=Arimo:wght@400;700&display=swap" rel="stylesheet">
<style>
  :root {
    --bg: #c4c4c4;
    --card-white: #ffffff;
    --teal: #4aa9c0;
    --teal-light: #8fd0df;
    --teal-deep: #3a9cb6;
    --mint: #9fd4b8;
    --ink: #2a2a2a;
    --rule: #7ec3c4;
  }
  * { margin: 0; padding: 0; box-sizing: border-box; }
  html, body { width: 1200px; height: 788px; overflow: hidden; }
  body {
    background: var(--bg);
    position: relative;
    font-family: "Arimo", Arial, sans-serif;
  }
  .card {
    position: absolute;
    top: 239px;
    width: 520px;
    height: 310px;
    border-radius: 22px;
    overflow: hidden;
    box-shadow: 0 10px 24px rgba(0,0,0,0.22);
  }
  /* Front card */
  .card-front { left: 50px; background: var(--card-white); }
  .brand-name {
    font-family: "Alegreya", Georgia, serif;
    font-weight: 500;
    letter-spacing: 0.5px;
    white-space: nowrap;
  }
  .card-front .brand {
    position: absolute;
    right: 42px;
    top: 52px;
    display: flex;
    align-items: center;
    gap: 8px;
  }
  .card-front .brand-mark {
    width: 12px; height: 12px; border-radius: 50%;
    background: var(--teal);
  }
  .card-front .brand-name { font-size: 34px; color: var(--teal); }
  .main-rule {
    position: absolute;
    left: 30px; right: 30px; top: 150px;
    height: 1px;
    background: linear-gradient(90deg, var(--teal), var(--mint) 60%, var(--rule));
  }
  .person {
    position: absolute;
    left: 34px; top: 112px;
  }
  .person-name {
    font-weight: 700;
    font-size: 20px;
    letter-spacing: 0.5px;
    color: var(--teal);
  }
  .person-role {
    position: absolute;
    left: 34px; top: 158px;
    font-size: 14px;
    color: var(--ink);
  }
  .contact-list {
    position: absolute;
    left: 34px; top: 192px;
    list-style: none;
    font-size: 13.5px;
    color: var(--ink);
    line-height: 21px;
  }
  .contact-list li { display: flex; align-items: center; gap: 8px; }
  .contact-list svg { width: 11px; height: 11px; fill: var(--teal); flex: none; }
  .address {
    position: absolute;
    right: 34px; top: 172px;
    font-size: 13.5px;
    line-height: 20px;
    color: var(--ink);
    text-align: left;
  }
  /* Back card */
  .card-back { left: 630px; }
  .card-back .wash {
    position: absolute; inset: 0;
    background: linear-gradient(135deg, #7cc5d6 0%, #5db5cb 45%, #86cddc 100%);
  }
  .card-back .brand {
    position: absolute;
    left: 0; right: 0; top: 0; bottom: 0;
    display: flex; align-items: center; justify-content: center;
    gap: 12px;
  }
  .card-back .brand-mark {
    width: 16px; height: 16px; border-radius: 50%;
    background: var(--card-white);
  }
  .card-back .brand-name { font-size: 52px; color: var(--card-white); }
</style>
</head>
<body>

  <section class="card card-front" aria-label="Business card front">
    <div class="brand">
      <span class="brand-mark"></span>
      <span class="brand-name">little lanterns</span>
    </div>

    <div class="person">
      <div class="person-name">DANIEL HARPER</div>
    </div>
    <div class="main-rule"></div>
    <div class="person-role">CEO/Founder</div>

    <ul class="contact-list">
      <li>
        <svg viewBox="0 0 24 24"><path d="M6.6 10.8a15.1 15.1 0 0 0 6.6 6.6l2.2-2.2a1 1 0 0 1 1-.25 11.4 11.4 0 0 0 3.6.57 1 1 0 0 1 1 1V20a1 1 0 0 1-1 1A17 17 0 0 1 3 4a1 1 0 0 1 1-1h3.5a1 1 0 0 1 1 1c0 1.25.2 2.45.57 3.6a1 1 0 0 1-.25 1z"/></svg>
        (00) 3826 1594
      </li>
      <li>
        <svg viewBox="0 0 24 24"><path d="M7 1h10a2 2 0 0 1 2 2v18a2 2 0 0 1-2 2H7a2 2 0 0 1-2-2V3a2 2 0 0 1 2-2zm0 3v14h10V4zm5 15.5a1 1 0 1 0 0 2 1 1 0 0 0 0-2z"/></svg>
        (00) 6091 4372
      </li>
      <li>
        <svg viewBox="0 0 24 24"><path d="M2 5h20v14H2zm2 2v.5l8 5 8-5V7zm0 2.8V17h16V9.8l-8 5z"/></svg>
        info@littlelanterns.com
      </li>
      <li>
        <svg viewBox="0 0 24 24"><path d="M12 2a10 10 0 1 0 0 20 10 10 0 0 0 0-20zm6.9 6h-2.9a15 15 0 0 0-1.4-3.6A8 8 0 0 1 18.9 8zM12 4c.8 1.1 1.5 2.5 1.9 4h-3.8c.4-1.5 1.1-2.9 1.9-4zM4.3 14a8 8 0 0 1 0-4h3.3a16 16 0 0 0 0 4zm.8 2h2.9c.3 1.3.8 2.5 1.4 3.6A8 8 0 0 1 5.1 16zM8 8H5.1a8 8 0 0 1 4.3-3.6C8.8 5.5 8.3 6.7 8 8zm4 12c-.8-1.1-1.5-2.5-1.9-4h3.8c-.4 1.5-1.1 2.9-1.9 4zm2.3-6H9.7a14 14 0 0 1 0-4h4.6a14 14 0 0 1 0 4zm.3 5.6c.6-1.1 1.1-2.3 1.4-3.6h2.9a8 8 0 0 1-4.3 3.6zm1.8-5.6a16 16 0 0 0 0-4h3.3a8 8 0 0 1 0 4z"/></svg>
        www.littlelanterns.com
      </li>
    </ul>

    <address class="address" style="font-style: normal;">
      Po Box 4512 Oak Street<br>
      Country Name, AB 31908
    </address>
  </section>

  <section class="card card-back" aria-label="Business card back">
    <div class="wash" role="img" aria-label="Soft blue watercolour wash background"></div>
    <div class="brand">
      <span class="brand-mark"></span>
      <span class="brand-name">little lanterns</span>
    </div>
  </section>

</body>
</html>
```